Recruiting ad for Caregivers and Nurses

We need a few amazing, fun, catchy, creative recruiting ads for Caregivers and Nurses to care for homecare patients on the island of Oahu, in Hawaii. We are an in home care company called Palmer Homecare. Our care services are provided 24/7, so we need staff that can work days, nights, weekdays, weekends. We need catchy fun ads to entice caregivers and nurses to call our office to inquire about jobs available. Our patients age range is from babies to seniors. We need caregivers and nurses for basic patient care (bathing, dressing, ambulating, preparing meals, medication reminders, light housekeeping) and complex patients (oxygen, tube feeding, injections, vents, wound care). Here are some bullets to consider including:
*Full-time and Part-time Positions Available (days, nights, weekdays, weekends)
*Sign-On Bonus Programs Offered up to $500
*Refer a Friend Bonus Program
*Holiday Pay
*2 Health Plans to Choose from
*Island-Wide Locations
*All PPE Provided (masks, gloves, etc)
*401K Program
*Tuition Benefits

```html
<!DOCTYPE html>
<html lang="en">
<head>
<meta charset="utf-8">
<title>Caregivers and Nurses – Palmer Homecare</title>
<link href="https://fonts.googleapis.com/css2?family=Marcellus&family=Cormorant+Garamond:ital,wght@1,500&family=Arimo:wght@400;700&display=swap" rel="stylesheet">
<style>
  :root {
    --page-bg: #9a99a2;
    --mint: #a6dcd6;
    --mint-soft: #e6f5f3;
    --coral: #f39a7e;
    --slate: #3d6473;
    --ink: #0f4d45;
    --white: #ffffff;
  }
  * { margin: 0; padding: 0; box-sizing: border-box; }
  html, body { width: 1200px; height: 1200px; overflow: hidden; }
  body { background: var(--page-bg); position: relative; font-family: "Arimo", Arial, sans-serif; }

  .flyer {
    position: absolute; left: 200px; top: 82px;
    width: 800px; height: 1035px; overflow: hidden;
    background: var(--white);
  }
  .flyer-inner {
    position: absolute; left: 0; top: 0;
    width: 640px; height: 828px;
    transform: scale(1.25); transform-origin: 0 0;
  }
  .backdrop { position: absolute; inset: 0; width: 640px; height: 828px; }

  .headline {
    position: absolute; left: 0; top: 14px; width: 640px;
    font-family: "Marcellus", serif; font-weight: 400; color: var(--ink);
  }
  .headline-main { position: absolute; left: 172px; top: 0; font-size: 52px; line-height: 1; }
  .headline-sub { position: absolute; left: 350px; top: 56px; font-size: 52px; line-height: 1; white-space: nowrap; }
  .headline-and {
    font-family: "Cormorant Garamond", serif; font-style: italic;
    color: var(--coral); font-size: 50px; margin-right: 6px;
  }

  .brand-badge {
    position: absolute; left: 422px; top: 348px; width: 200px; height: 200px;
    border-radius: 50%; background: var(--white);
    border: 4px solid var(--coral);
    box-shadow: 0 0 0 6px rgba(255,255,255,.7);
    display: flex; align-items: center; justify-content: center; text-align: center;
  }
  .brand-name {
    font-family: "Marcellus", serif; color: var(--ink);
    font-size: 30px; line-height: 1.05;
  }

  .role-icon {
    position: absolute; left: 20px; top: 418px; width: 50px; height: 50px;
    border-radius: 50%; border: 2px solid var(--slate); background: var(--mint-soft);
  }

  .positions { position: absolute; left: 20px; top: 480px; font-weight: 700; font-size: 19px; line-height: 24px; }
  .positions-top { color: var(--coral); }
  .positions-bottom { color: var(--ink); }
  .shift-pill {
    position: absolute; left: 17px; top: 533px; width: 275px; height: 23px;
    border-radius: 12px; background: var(--coral); color: var(--white);
    font-size: 13px; line-height: 23px; text-align: center;
  }

  .perks {
    position: absolute; left: 62px; top: 568px; width: 400px;
    list-style: none; text-align: center;
    font-size: 13px; line-height: 17px; color: var(--ink);
  }
  .perks li::before, .services li::before {
    content: ""; display: inline-block; width: 7px; height: 7px; border-radius: 50%;
    background: var(--coral); margin-right: 6px; vertical-align: 1px;
  }
  .perks b { font-weight: 700; }

  .services {
    position: absolute; left: 12px; top: 715px; width: 275px;
    list-style: none; color: var(--white); font-size: 12px; line-height: 14.5px;
  }
  .services b { color: var(--coral); }
  .services .detail { display: block; padding-left: 13px; }

  .contact { position: absolute; left: 362px; top: 730px; width: 270px; color: var(--ink); }
  .contact-label { font-family: "Marcellus", serif; font-size: 30px; text-align: right; padding-right: 10px; }
  .contact-phone {
    display: flex; align-items: center; gap: 8px; margin-top: 6px;
    color: var(--white); font-size: 32px; white-space: nowrap;
  }
  .phone-icon { width: 34px; height: 34px; flex: none; }
</style>
</head>
<body>
  <div class="flyer">
    <div class="flyer-inner">
      <svg class="backdrop" viewBox="0 0 640 828" aria-hidden="true">
        <defs>
          <linearGradient id="photoTone" x1="0" y1="0" x2="1" y2="1">
            <stop offset="0" stop-color="#d9d4cf"/>
            <stop offset=".5" stop-color="#e9e2d8"/>
            <stop offset="1" stop-color="#c9c2b8"/>
          </linearGradient>
          <linearGradient id="topBand" x1="0" y1="0" x2="1" y2="0">
            <stop offset="0" stop-color="#a6dcd6"/>
            <stop offset=".45" stop-color="#f4fbfa"/>
            <stop offset="1" stop-color="#a6dcd6"/>
          </linearGradient>
        </defs>
        <rect x="0" y="0" width="640" height="590" fill="url(#photoTone)" role="img" aria-label="Photo of a caregiver sharing a tablet with a smiling senior woman at home"/>
        <path d="M0 0 H640 V215 C560 170 470 140 380 130 C250 115 120 60 0 40 Z" fill="url(#topBand)"/>
        <path d="M0 0 H150 C110 5 50 20 0 35 Z" fill="var(--coral)"/>
        <path d="M430 132 C520 148 590 172 640 196 V245 C590 215 520 178 430 132 Z" fill="var(--coral)"/>
        <path d="M0 330 C80 380 200 430 340 470 C420 490 520 540 640 560 V828 H0 Z" fill="var(--mint)"/>
        <path d="M0 350 C90 400 210 450 350 485 C430 505 530 555 640 575 V828 H0 Z" fill="var(--white)"/>
        <path d="M0 708 H350 C320 740 292 790 272 828 H0 Z" fill="var(--slate)"/>
        <path d="M262 828 C360 740 500 700 640 672 V828 Z" fill="var(--mint)"/>
        <path d="M300 828 C390 765 510 730 640 705 V828 Z" fill="var(--coral)"/>
      </svg>

      <h1 class="headline">
        <span class="headline-main">Caregivers</span>
        <span class="headline-sub"><span class="headline-and">and</span>Nurses</span>
      </h1>

      <div class="brand-badge"><p class="brand-name">Palmer<br>Homecare</p></div>

      <div class="role-icon" role="img" aria-label="Nurse icon"></div>

      <h2 class="positions">
        <span class="positions-top">FULL-TIME &amp; PART-TIME</span><br>
        <span class="positions-bottom">POSITIONS AVAILABLE</span>
      </h2>
      <p class="shift-pill">(Days, Nights, Weekdays, Weekends)</p>

      <ul class="perks">
        <li><b>SIGN-ON BONUS PROGRAMS -</b> Offered up to $500</li>
        <li><b>REFER A FRIEND BONUS PROGRAM</b></li>
        <li><b>HOLIDAY PAY</b></li>
        <li><b>2 HEALTH PLANS</b> to choose from</li>
        <li>Island-Wide Locations</li>
        <li><b>All PPE Provided</b> (Masks, gloves, etc)</li>
        <li><b>401K PROGRAM</b></li>
        <li><b>TUITION BENEFITS</b></li>
      </ul>

      <ul class="services">
        <li><b>BABIES TO SENIORS</b></li>
        <li><b>BASIC PATIENT CARE</b>
          <span class="detail">(bathing, dressing, ambulating, preparing meals, medication reminders, light housekeeping)</span></li>
        <li><b>COMPLEX PATIENTS</b>
          <span class="detail">(oxygen, tube feeding, injections, vents, wound care).</span></li>
      </ul>

      <div class="contact">
        <p class="contact-label">Call Us</p>
        <p class="contact-phone">
          <svg class="phone-icon" viewBox="0 0 34 34" aria-hidden="true">
            <circle cx="17" cy="17" r="16" fill="var(--slate)"/>
            <path d="M11.5 9.5 l3 -0.5 l1.6 4 l-2 1.4 c0.9 2 2.5 3.6 4.5 4.5 l1.4 -2 l4 1.6 l-0.5 3 c-0.2 1 -1.1 1.5 -2 1.4 C15.5 22.2 11.8 18.5 11 12.5 c-0.1 -0.9 0.4 -1.8 0.5 -3 z" fill="var(--white)"/>
          </svg>
          808-555-0142
        </p>
      </div>
    </div>
  </div>
</body>
</html>
```